Store Front Sign for Vape Store

Interested in getting a store front sign graphic done. Sign is for over the door (lighted sign). Dimensions of sign: 6 feet long x 2 feet high.
Sign is for a Vape Store. I have attached the logo to be used.
Looking for a modern and professional look
Phone numbers to be used.
Whatsapp# 394-6150
Contact #562-7038
Sign should have Instagram & Facebook logos and. handle @lumoramists

Industry/Entity Type

Vape | Electronic Cigarettes

Colors

Designer to choose colors to be used in the design.

Requirements
Must have
• Facebook and Instagram Logos. Contact Numbers.
Should not have
• Any Persons.

```html
<!DOCTYPE html>
<html lang="en">
<head>
<meta charset="utf-8">
<title>Lumora Mists – Store Front Sign</title>
<link href="https://fonts.googleapis.com/css2?family=Montserrat:wght@500;600;700&family=Allura&display=swap" rel="stylesheet">
<style>
  :root {
    --page: #e9e8e9;
    --peach: #f7b08a;
    --coral: #ef5a4a;
    --hot-pink: #e2185c;
    --magenta: #d1177f;
    --purple: #8a2a8e;
    --white: #ffffff;
    --ink-bar: #1f1d20;
    --device-dark: #2b3340;
    --device-red: #b3202a;
    --logo-ring: #111216;
    --logo-accent: #1e7fc4;
  }
  * { box-sizing: border-box; margin: 0; padding: 0; }
  html, body { width: 1117px; height: 1200px; overflow: hidden; background: var(--page); }
  .canvas { position: relative; width: 1117px; height: 1200px; }

  .sign {
    position: absolute; left: 40px; top: 427px; width: 1037px; height: 346px;
    overflow: hidden;
    background:
      radial-gradient(ellipse 260px 200px at 120px 140px, rgba(255,220,190,.55), transparent 70%),
      radial-gradient(ellipse 300px 140px at 560px 40px, rgba(255,255,255,.18), transparent 70%),
      linear-gradient(100deg, var(--peach) 0%, var(--coral) 20%, var(--hot-pink) 42%, var(--magenta) 65%, var(--purple) 100%);
    font-family: "Montserrat", sans-serif; color: var(--white);
  }

  .product-photo {
    position: absolute; border-radius: 16px;
    background: linear-gradient(160deg, #3a3f4a 0%, var(--device-dark) 45%, var(--device-red) 100%);
  }
  .product-photo--top-left { left: -70px; top: 20px; width: 150px; height: 260px; transform: rotate(-38deg); }
  .product-photo--bottom-left { left: 90px; top: 250px; width: 140px; height: 230px; transform: rotate(40deg); }
  .product-photo--right { left: 780px; top: 14px; width: 220px; height: 320px; border-radius: 22px; transform: rotate(10deg);
    background: linear-gradient(165deg, #1c1d22 0%, #3b4250 30%, var(--device-dark) 70%, var(--device-red) 100%); }

  .brand-badge {
    position: absolute; left: 184px; top: 45px; width: 150px; height: 150px; border-radius: 50%;
    background: var(--logo-ring); border: 4px solid var(--white);
    box-shadow: inset 0 0 0 4px var(--logo-accent);
    display: flex; align-items: center; justify-content: center; text-align: center;
    font-weight: 600; font-size: 22px; line-height: 1.15;
  }

  .welcome {
    position: absolute; left: 358px; top: 95px;
    font-weight: 500; font-size: 39px; line-height: 34px; letter-spacing: .5px; text-transform: uppercase;
  }
  .welcome span { display: block; }
  .shop-word {
    position: absolute; left: 520px; top: 10px;
    font-family: "Allura", cursive; font-size: 190px; line-height: 1; transform: rotate(-6deg);
  }

  .whatsapp {
    position: absolute; left: 0; width: 1037px; top: 218px; text-align: center;
    font-weight: 700; font-size: 29px;
  }
  .dot { display: inline-block; width: 24px; height: 24px; border-radius: 50%; vertical-align: -3px; margin-right: 6px; }
  .dot--green { background: #2fbf4a; }
  .dot--blue { background: #3b5ba8; }
  .dot--orange { background: #e8506b; }

  .contact-row {
    position: absolute; left: 275px; top: 252px; width: 485px;
    display: flex; align-items: center; gap: 12px;
    font-weight: 600; font-size: 28px; white-space: nowrap;
  }
  .contact-row .rule { flex: 1; height: 2px; background: var(--white); }

  .social-bar {
    position: absolute; left: 303px; top: 288px; width: 431px; height: 44px;
    background: var(--ink-bar);
    display: flex; align-items: center; justify-content: center; gap: 6px;
    font-weight: 500; font-size: 23px;
  }
  .social-bar .handle { margin-left: 4px; }
</style>
</head>
<body>
<main class="canvas">
  <section class="sign" aria-label="Lumora Mists store front sign">
    <div class="product-photo product-photo--top-left" role="img" aria-label="Photo of a vape mod device"></div>
    <div class="product-photo product-photo--bottom-left" role="img" aria-label="Photo of a vape mod device"></div>
    <div class="product-photo product-photo--right" role="img" aria-label="Photo of two vape mod devices with tanks"></div>

    <div class="brand-badge">Lumora<br>Mists</div>

    <h1 class="welcome"><span>Welcome</span><span>to our</span></h1>
    <div class="shop-word">Shop!</div>

    <p class="whatsapp"><span class="dot dot--green"></span>394-6150</p>

    <p class="contact-row"><span class="rule"></span>Contact #562-7038<span class="rule"></span></p>

    <p class="social-bar">
      <span class="dot dot--blue"></span>
      <span class="dot dot--orange"></span>
      <span class="handle">/handle @lumoramists</span>
    </p>
  </section>
</main>
</body>
</html>
```